Business Card Design needed for start up company Halvora

In need of a new business card designed for a start up company based in Sydney, Halvora is a new start up innovative Company, our mission it to make property accessible for everyday Australian and to become the leading Real Estate platform in Australia. We want it to be fresh and clean.

Industry/Entity Type

Financial

Contact Information for Business Card

Section for Name
Section for Title

HALVORA - The Strength of Pooling
Mobile:
Direct:

Font styles to use
Sans Serif

Colors
33a6d7
0692cd
0255a3
ffffff

Requirements
Must have
• Logo, all business card details

```html
<!DOCTYPE html>
<html lang="en">
<head>
<meta charset="utf-8">
<title>Halvora Business Card</title>
<link rel="stylesheet" href="https://fonts.googleapis.com/css2?family=Lato:wght@400;700;900&display=swap">
<style>
  :root {
    --cyan: #33a6d7;
    --sky: #0692cd;
    --navy: #0255a3;
    --navy-deep: #024a8e;
    --white: #ffffff;
    --paper: #f4f5f6;
    --stage: #e6e8eb;
    --ink-soft: #dfe9f4;
  }
  * { box-sizing: border-box; margin: 0; padding: 0; }
  html, body {
    width: 1200px; height: 780px; overflow: hidden;
    background: var(--stage);
    font-family: "Lato", "Helvetica Neue", Arial, sans-serif;
  }
  .canvas {
    width: 1200px; height: 780px;
    display: flex; align-items: center; justify-content: center; gap: 60px;
  }
  .card {
    width: 525px; height: 300px; position: relative; overflow: hidden;
    box-shadow: 0 14px 30px rgba(2, 40, 80, 0.18);
  }

  /* Front side */
  .card-front { background: var(--paper); }
  .front-brand {
    position: absolute; left: 40px; top: 46px;
    display: flex; align-items: center; gap: 16px;
  }
  .brand-dot {
    width: 58px; height: 58px; border-radius: 50%; background: var(--cyan);
  }
  .brand-name {
    font-weight: 900; font-size: 56px; letter-spacing: -1px; line-height: 1;
    color: var(--navy);
  }
  .identity-strip {
    position: absolute; left: 0; right: 0; top: 158px; height: 34px;
    background: var(--cyan);
    display: flex; align-items: center; padding-left: 40px;
    color: var(--white);
  }
  .person-name { font-weight: 900; font-size: 17px; letter-spacing: 0.3px; }
  .divider { width: 1px; height: 18px; background: var(--white); margin: 0 12px; opacity: 0.85; }
  .person-title { font-weight: 400; font-size: 15px; }
  .contact-panel {
    position: absolute; left: 0; right: 0; top: 192px; bottom: 0;
    background: linear-gradient(180deg, var(--navy) 0%, var(--navy-deep) 100%);
    padding: 16px 40px 0; color: var(--white);
  }
  .contact-line {
    display: flex; align-items: center; gap: 9px;
    font-size: 15px; font-weight: 400; line-height: 22px;
  }
  .contact-icon {
    width: 15px; height: 15px; border-radius: 2px; background: var(--cyan);
    display: flex; align-items: center; justify-content: center;
  }
  .tagline { margin-top: 12px; font-size: 15px; font-weight: 700; color: var(--ink-soft); }

  /* Back side */
  .card-back {
    background: radial-gradient(ellipse at 50% 45%, #2a6fb6 0%, var(--navy) 60%, var(--navy-deep) 100%);
    display: flex; align-items: center; justify-content: center;
  }
  .back-brand { display: flex; align-items: center; gap: 18px; }
  .back-brand .brand-dot { width: 72px; height: 72px; }
  .back-brand .brand-name { color: var(--white); font-size: 66px; }
</style>
</head>
<body>
<main class="canvas">

  <section class="card card-front" aria-label="Business card front">
    <div class="front-brand">
      <span class="brand-dot"></span>
      <span class="brand-name">HALVORA</span>
    </div>

    <div class="identity-strip">
      <span class="person-name">JONAH REEVE</span>
      <span class="divider"></span>
      <span class="person-title">Managing Director</span>
    </div>

    <div class="contact-panel">
      <p class="contact-line">
        <span class="contact-icon" aria-label="Mobile">
          <svg width="9" height="12" viewBox="0 0 9 12"><rect x="1" y="0.5" width="7" height="11" rx="1.2" fill="none" stroke="#fff" stroke-width="1.2"/><circle cx="4.5" cy="9.3" r="0.8" fill="#fff"/></svg>
        </span>
        415.208.3367
      </p>
      <p class="contact-line">
        <span class="contact-icon" aria-label="Direct">
          <svg width="11" height="11" viewBox="0 0 12 12"><path d="M2.5 1 L4.5 1 L5.3 3.6 L4 4.6 C4.7 6.1 5.9 7.3 7.4 8 L8.4 6.7 L11 7.5 L11 9.5 C11 10.3 10.3 11 9.5 11 C5 11 1 7 1 2.5 C1 1.7 1.7 1 2.5 1 Z" fill="#fff"/></svg>
        </span>
        415.208.3367
      </p>
      <p class="tagline">HALVORA - The Strength of Pooling</p>
    </div>
  </section>

  <section class="card card-back" aria-label="Business card back">
    <div class="back-brand">
      <span class="brand-dot"></span>
      <span class="brand-name">HALVORA</span>
    </div>
  </section>

</main>
</body>
</html>
```